We need a business card design for a new company located in Missouri City, TX, entitled 'BrightPath Chiropractic & Holistic Center'. Our services include restoration of health and vitality, spinal exam, health assessment, dietary & fitness programs, lymphatic & therapeutic massage, detox & remineralize body wraps, far infrared sauna therapy

Industry/Entity Type

Business

Contact Information for Business Card

BrightPath Chiropractic & Holistic Center, Marlene Okafor LMT, 4215 Elm Ridge Rd., Suite 310, Missouri City, TX 77482, 281-555-0193

```html
<!DOCTYPE html>
<html lang="en">
<head>
<meta charset="utf-8">
<title>BrightPath Chiropractic &amp; Holistic Center – Business Card</title>
<link href="https://fonts.googleapis.com/css2?family=Old+Standard+TT:ital,wght@0,400;0,700;1,400&family=Open+Sans:wght@400&display=swap" rel="stylesheet">
<style>
  :root {
    --page: #ece8e2;
    --white: #ffffff;
    --ink: #000000;
    --navy: #1d5a86;
    --teal: #1a9882;
    --teal-dark: #0f3f36;
    --grey: #b9b9b9;
    --serif: "Old Standard TT", Georgia, serif;
    --sans: "Open Sans", Arial, sans-serif;
  }
  * { box-sizing: border-box; margin: 0; padding: 0; }
  html, body { width: 1200px; height: 902px; overflow: hidden; }
  body { background: var(--page); position: relative; }
  .card {
    position: absolute;
    left: 240px;
    width: 720px;
    height: 411px;
    overflow: hidden;
    box-shadow: 0 6px 18px rgba(0,0,0,.18);
  }

  /* Back side: services */
  .card-back { top: 30px; background: var(--teal); }
  .services-title {
    position: absolute; left: 48px; top: 40px;
    font-family: var(--serif); font-weight: 700; font-size: 44px; color: var(--ink);
  }
  .services-rule {
    position: absolute; left: 44px; top: 100px; width: 636px; height: 2px;
    background: var(--ink);
  }
  .services-list { position: absolute; left: 60px; top: 116px; list-style: none; }
  .services-list li {
    display: flex; align-items: center; gap: 18px;
    font-family: var(--serif); font-size: 28px; line-height: 39px; color: var(--teal-dark);
  }
  .services-list svg { flex: none; }

  /* Front side: contact */
  .card-front { top: 461px; background: var(--white); }
  .wave { position: absolute; inset: 0; }
  .holder-name {
    position: absolute; right: 40px; top: 16px;
    font-family: var(--serif); font-weight: 400; font-size: 44px; line-height: 56px; color: var(--navy);
  }
  .holder-title {
    position: absolute; right: 42px; top: 72px;
    font-family: var(--serif); font-style: italic; font-size: 22px; line-height: 28px; color: #222;
  }
  .contact {
    position: absolute; right: 36px; top: 162px; list-style: none; text-align: right;
    font-family: var(--sans); font-size: 16px; line-height: 26px; color: var(--white);
  }
  .contact li { display: flex; justify-content: flex-end; align-items: flex-start; gap: 8px; }
  .contact svg { flex: none; margin-top: 6px; }
  .contact .address { max-width: 320px; }
  .brand { position: absolute; left: 42px; top: 286px; }
  .brand-name {
    display: flex; align-items: center; gap: 12px;
    font-family: var(--serif); font-size: 40px; line-height: 48px; color: var(--white);
  }
  .brand-dot { width: 16px; height: 16px; border-radius: 50%; background: var(--teal); }
  .brand-tagline {
    margin-top: 6px;
    font-family: var(--sans); font-size: 22px; color: var(--grey);
  }
</style>
</head>
<body>

<section class="card card-back" aria-label="Card back: services">
  <h2 class="services-title">Services</h2>
  <div class="services-rule"></div>
  <ul class="services-list">
    <li><svg width="16" height="16" viewBox="0 0 16 16"><circle cx="8" cy="8" r="6" fill="none" stroke="#0f3f36" stroke-width="1.5"/><circle cx="8" cy="8" r="2" fill="#0f3f36"/></svg>restoration of health and vitality</li>
    <li><svg width="16" height="16" viewBox="0 0 16 16"><circle cx="8" cy="8" r="6" fill="none" stroke="#0f3f36" stroke-width="1.5"/><circle cx="8" cy="8" r="2" fill="#0f3f36"/></svg>spinal exam</li>
    <li><svg width="16" height="16" viewBox="0 0 16 16"><circle cx="8" cy="8" r="6" fill="none" stroke="#0f3f36" stroke-width="1.5"/><circle cx="8" cy="8" r="2" fill="#0f3f36"/></svg>health assessment</li>
    <li><svg width="16" height="16" viewBox="0 0 16 16"><circle cx="8" cy="8" r="6" fill="none" stroke="#0f3f36" stroke-width="1.5"/><circle cx="8" cy="8" r="2" fill="#0f3f36"/></svg>dietary &amp; fitness programs</li>
    <li><svg width="16" height="16" viewBox="0 0 16 16"><circle cx="8" cy="8" r="6" fill="none" stroke="#0f3f36" stroke-width="1.5"/><circle cx="8" cy="8" r="2" fill="#0f3f36"/></svg>lymphatic &amp; therapeutic massage</li>
    <li><svg width="16" height="16" viewBox="0 0 16 16"><circle cx="8" cy="8" r="6" fill="none" stroke="#0f3f36" stroke-width="1.5"/><circle cx="8" cy="8" r="2" fill="#0f3f36"/></svg>detox &amp; remineralize body wraps</li>
    <li><svg width="16" height="16" viewBox="0 0 16 16"><circle cx="8" cy="8" r="6" fill="none" stroke="#0f3f36" stroke-width="1.5"/><circle cx="8" cy="8" r="2" fill="#0f3f36"/></svg>far infrared sauna therapy</li>
  </ul>
</section>

<section class="card card-front" aria-label="Card front: contact details">
  <svg class="wave" width="720" height="411" viewBox="0 0 720 411" aria-hidden="true">
    <path d="M0,222 C200,224 320,162 430,142 C540,124 640,126 720,124" fill="none" stroke="#1d5a86" stroke-width="9"/>
    <path d="M0,236 C200,238 320,176 430,156 C540,138 640,140 720,138 L720,411 L0,411 Z" fill="#000"/>
  </svg>

  <h1 class="holder-name">Dana Whitfield</h1>
  <p class="holder-title">Chief Executive</p>

  <ul class="contact">
    <li>281-555-0193
      <svg width="13" height="13" viewBox="0 0 13 13"><rect width="13" height="13" rx="2" fill="#fff"/><path d="M3.5,2.5 L5,2.5 L5.8,4.8 L4.8,5.6 C5.4,7 6,7.6 7.4,8.2 L8.2,7.2 L10.5,8 L10.5,9.5 C7,10 3,6 3.5,2.5Z" fill="#000"/></svg></li>
    <li>dana.whitfield@brightpathcare.com
      <svg width="13" height="13" viewBox="0 0 13 13"><rect width="13" height="13" rx="2" fill="#fff"/><rect x="2.5" y="4" width="8" height="5.5" fill="none" stroke="#000"/><path d="M2.5,4 L6.5,7 L10.5,4" fill="none" stroke="#000"/></svg></li>
    <li>www.brightpathcare.com
      <svg width="13" height="13" viewBox="0 0 13 13"><rect width="13" height="13" rx="2" fill="#fff"/><circle cx="6.5" cy="6.5" r="4" fill="none" stroke="#000"/><path d="M2.5,6.5 H10.5 M6.5,2.5 V10.5" stroke="#000"/></svg></li>
    <li><span class="address">Marlene Okafor LMT, 4215 Elm Ridge Rd., Suite 310, Missouri City, TX 77482</span>
      <svg width="13" height="13" viewBox="0 0 13 13"><rect width="13" height="13" rx="2" fill="#fff"/><path d="M6.5,11 C4,7.5 3.5,6.5 3.5,5.2 A3,3 0 0 1 9.5,5.2 C9.5,6.5 9,7.5 6.5,11Z" fill="#000"/><circle cx="6.5" cy="5.2" r="1.1" fill="#fff"/></svg></li>
  </ul>

  <div class="brand">
    <div class="brand-name"><span class="brand-dot"></span>BrightPath</div>
    <div class="brand-tagline">Chiropractic &amp; Holistic Center</div>
  </div>
</section>

</body>
</html>
```